Business Card Design

Business Card for professional consulting firm working with large financial institutions.

Target Market(s)

Executive buyers

Industry/Entity Type

Banking

Contact Information for Business Card

Mild creativity wanted. Not boring, but do elaborate artwork.

Font styles to use
Serif
Sans Serif

Colors

Designer to choose colors to be used in the design.

Requirements
Must have
• Standard business card features - company name, individual name, telephone, website, email, locations.
Nice to have
• Two colors
Should not have
• too many colors, fancy printing, cartoons.

```html
<!DOCTYPE html>
<html lang="en">
<head>
<meta charset="utf-8">
<title>Kelmont Partners – Business Card</title>
<link rel="stylesheet" href="https://fonts.googleapis.com/css2?family=Roboto:wght@400;500&family=Roboto+Condensed:wght@700&display=swap">
<style>
  :root {
    --backdrop: #2b2b2d;
    --card: #1f1f20;
    --ink: #ffffff;
    --ink-soft: #e6e6e6;
    --rule: #bdbdbd;
  }
  * { margin: 0; padding: 0; box-sizing: border-box; }
  html, body { width: 1200px; height: 900px; overflow: hidden; }
  body {
    background: var(--backdrop);
    font-family: "Roboto", Arial, sans-serif;
    color: var(--ink);
    position: relative;
  }
  .card {
    position: absolute;
    left: 285px;
    width: 630px;
    height: 360px;
    background: var(--card);
    border-radius: 3px;
  }
  .card--front { top: 65px; }
  .card--back  { top: 475px; }

  /* Front */
  .brand {
    position: absolute;
    left: 0; right: 0; top: 120px;
    display: flex; align-items: center; justify-content: center; gap: 14px;
  }
  .brand__dot {
    width: 14px; height: 14px; border-radius: 50%;
    background: var(--ink);
  }
  .brand__name {
    font-family: "Roboto", Arial, sans-serif;
    font-weight: 500;
    font-size: 42px;
    letter-spacing: 0.5px;
    color: var(--ink);
  }
  .front-web {
    position: absolute;
    left: 0; right: 0; top: 232px;
    text-align: center;
    font-size: 14px;
    letter-spacing: 7px;
    color: var(--ink-soft);
  }

  /* Back */
  .person {
    position: absolute;
    right: 375px; top: 120px;
    text-align: right;
  }
  .person__name {
    font-family: "Roboto Condensed", "Arial Narrow", sans-serif;
    font-weight: 700;
    font-size: 30px;
    line-height: 1;
    letter-spacing: 0.3px;
  }
  .person__role {
    margin-top: 6px;
    font-size: 15px;
    font-weight: 500;
    letter-spacing: 0.3px;
    color: var(--ink-soft);
  }
  .divider {
    position: absolute;
    left: 275px; top: 110px;
    width: 1px; height: 85px;
    background: var(--rule);
  }
  .contacts {
    position: absolute;
    left: 300px; top: 120px;
    list-style: none;
  }
  .contacts li {
    display: flex; align-items: center; gap: 10px;
    font-size: 15px; line-height: 20px;
    margin-bottom: 2px;
  }
  .contacts svg, .address svg { flex: none; fill: var(--ink); }
  .address {
    position: absolute;
    left: 60px; top: 270px;
    display: flex; align-items: center; gap: 6px;
    font-size: 16px;
  }
</style>
</head>
<body>

<section class="card card--front" aria-label="Card front">
  <div class="brand">
    <span class="brand__dot"></span>
    <span class="brand__name">Kelmont Partners</span>
  </div>
  <p class="front-web">www.kelmontpartners.com</p>
</section>

<section class="card card--back" aria-label="Card back">
  <div class="person">
    <p class="person__name">DANIEL REYES</p>
    <p class="person__role">CEO/FOUNDER</p>
  </div>
  <div class="divider"></div>
  <ul class="contacts">
    <li>
      <svg width="14" height="14" viewBox="0 0 24 24" aria-hidden="true"><path d="M6.6 10.8a15.1 15.1 0 0 0 6.6 6.6l2.2-2.2c.3-.3.7-.4 1-.2 1.1.4 2.3.6 3.6.6.6 0 1 .4 1 1V20c0 .6-.4 1-1 1A17 17 0 0 1 3 4c0-.6.4-1 1-1h3.5c.6 0 1 .4 1 1 0 1.3.2 2.5.6 3.6.1.3 0 .7-.2 1z"/></svg>
      <span>555 214 0187</span>
    </li>
    <li>
      <svg width="14" height="11" viewBox="0 0 24 18" aria-hidden="true"><path d="M0 0h24v18H0z M2 2v.6l10 6.4 10-6.4V2z" fill-rule="evenodd"/></svg>
      <span>info@kelmontpartners.com</span>
    </li>
    <li>
      <svg width="14" height="14" viewBox="0 0 24 24" aria-hidden="true"><path d="M12 2a10 10 0 1 0 0 20 10 10 0 0 0 0-20zm-1 17.9A8 8 0 0 1 4.2 10L9 14.8v1c0 1.1.9 2 2 2zm6.9-2.5c-.3-.8-1-1.4-1.9-1.4h-1v-3c0-.6-.4-1-1-1H8v-2h2c.6 0 1-.4 1-1V7h2c1.1 0 2-.9 2-2v-.4a8 8 0 0 1 2.9 12.8z"/></svg>
      <span>www.kelmontpartners.com</span>
    </li>
  </ul>
  <p class="address">
    <svg width="13" height="17" viewBox="0 0 24 32" aria-hidden="true"><path d="M12 0a12 12 0 0 0-12 12c0 9 12 20 12 20s12-11 12-20A12 12 0 0 0 12 0zm0 17a5 5 0 1 1 0-10 5 5 0 0 1 0 10z"/></svg>
    <span>1420 Harbor Ridge Road, Juneau, Alaska 99801</span>
  </p>
</section>

</body>
</html>
```